Bramble firearms training and consulting

Business card for a new firearms training company. I train persons on firearms safety, personal protection, shooting tactics and CHL.Im a Prior State trooper. I also served 4 years in IRaq as a Protection contractor with the Dept of State. Real world training for Real world situations. I would like the company name to be, BRAMBLE FIREARMS TRAINING AND CONSULTING. Im native american also. Ive provided pics. Put the name Bramble above the arrowhead but rotate the arrowhead to the right with it pointing right. Then place bramble inside the arrowhead. lets see both.
Industry/Entity Type
Business
Contact Information for Business Card
Christian Chatellier817-240-0488shadowtraining33@gmail.com

```html
<!DOCTYPE html>
<html lang="en">
<head>
<meta charset="utf-8">
<title>Bramble Firearms Training and Consulting — Business Card</title>
<link rel="stylesheet" href="https://fonts.googleapis.com/css2?family=Rye&display=swap">
<style>
  :root {
    --backdrop: #141414;
    --card: #f7f7f5;
    --brand-red: #7a1408;
    --ink: #1c1c1c;
    --band-line: #f2e9e6;
  }
  html, body {
    margin: 0;
    padding: 0;
    width: 1200px;
    height: 868px;
    overflow: hidden;
    background: var(--backdrop);
  }
  .canvas {
    position: relative;
    width: 1200px;
    height: 868px;
  }
  .business-card {
    position: absolute;
    left: 360px;
    top: 44px;
    width: 480px;
    height: 780px;
    background: var(--card);
    color: var(--ink);
    text-align: center;
  }
  .accent-band {
    position: absolute;
    left: 124px;
    width: 232px;
    height: 36px;
    background: var(--brand-red);
  }
  .accent-band::after {
    content: "";
    position: absolute;
    left: 0;
    right: 0;
    height: 2px;
    background: var(--band-line);
  }
  .accent-band--top { top: 0; }
  .accent-band--top::after { bottom: 7px; }
  .accent-band--bottom { bottom: 0; }
  .accent-band--bottom::after { top: 7px; }

  .holder-name {
    position: absolute;
    top: 66px;
    left: 0;
    right: 0;
    margin: 0;
    font-family: "Rye", serif;
    font-weight: 400;
    font-size: 23px;
    letter-spacing: 1px;
  }
  .holder-role {
    position: absolute;
    top: 100px;
    left: 0;
    right: 0;
    margin: 0;
    font-family: "Rye", serif;
    font-size: 10px;
    letter-spacing: 0.5px;
  }
  .brand-lockup {
    position: absolute;
    top: 318px;
    left: 0;
    right: 0;
    display: flex;
    justify-content: center;
    align-items: center;
    gap: 16px;
    height: 70px;
  }
  .brand-mark {
    width: 44px;
    height: 44px;
    flex: none;
  }
  .brand-name {
    margin: 0;
    font-family: "Rye", serif;
    font-weight: 400;
    font-size: 48px;
    letter-spacing: 3px;
    line-height: 1;
    color: var(--brand-red);
  }
  .brand-tagline {
    position: absolute;
    top: 430px;
    left: 0;
    right: 0;
    margin: 0;
    font-family: "Rye", serif;
    font-size: 14px;
    letter-spacing: 0.5px;
    color: var(--brand-red);
  }
  .contact-list {
    position: absolute;
    top: 618px;
    left: 0;
    right: 0;
    margin: 0;
    padding: 0;
    list-style: none;
    font-family: "Rye", serif;
    font-size: 16px;
    letter-spacing: 0.5px;
  }
  .contact-item {
    display: flex;
    justify-content: center;
    align-items: center;
    gap: 8px;
    height: 31px;
  }
  .contact-icon {
    width: 17px;
    height: 17px;
    flex: none;
  }
</style>
</head>
<body>
<main class="canvas">
  <article class="business-card">
    <div class="accent-band accent-band--top"></div>

    <h1 class="holder-name">DORIAN PELLWICK</h1>
    <p class="holder-role">TRAINER AND CONSULTANT</p>

    <div class="brand-lockup">
      <svg class="brand-mark" viewBox="0 0 44 44" role="img" aria-label="Bramble brand mark">
        <circle cx="22" cy="22" r="21" fill="#7a1408"/>
      </svg>
      <p class="brand-name">BRAMBLE</p>
    </div>
    <p class="brand-tagline">BRAMBLE FIREARMS TRAINING AND CONSULTING</p>

    <ul class="contact-list">
      <li class="contact-item">
        <svg class="contact-icon" viewBox="0 0 20 20" aria-hidden="true">
          <circle cx="10" cy="10" r="9" fill="none" stroke="#1c1c1c" stroke-width="1.6"/>
          <path d="M6.5 5.5l2 0 1 2.5-1.3 1c.6 1.3 1.5 2.2 2.8 2.8l1-1.3 2.5 1v2c-4.5.3-8.3-3.5-8-8z" fill="#1c1c1c"/>
        </svg>
        <span>555-317-9062</span>
      </li>
      <li class="contact-item">
        <svg class="contact-icon" viewBox="0 0 20 20" aria-hidden="true">
          <circle cx="10" cy="10" r="9.5" fill="#1c1c1c"/>
          <rect x="5" y="6.5" width="10" height="7" fill="#f7f7f5"/>
          <path d="M5 6.5l5 4 5-4" fill="none" stroke="#1c1c1c" stroke-width="1.2"/>
        </svg>
        <span>BRAMBLECOURSE58@MAILVENTO.COM</span>
      </li>
      <li class="contact-item">
        <svg class="contact-icon" viewBox="0 0 20 20" aria-hidden="true">
          <circle cx="10" cy="10" r="9.5" fill="#1c1c1c"/>
          <path d="M10 4.5l5.5 5h-1.7v5h-2.6v-3h-2.4v3H6.2v-5H4.5z" fill="#f7f7f5"/>
        </svg>
        <span>48 LINDEN ROW, MARLOW, NY 12904</span>
      </li>
    </ul>

    <div class="accent-band accent-band--bottom"></div>
  </article>
</main>
</body>
</html>
```